Brisk Fixwell business card

I need business card for my business, I think you have all my details.six months ago I design with you car wrap design. We would like to design both side of the card. On front of card we would like logo , Name and our contact details.
At the back we are looking to mentioned our services.
The name will be:
Faridoullan Mestor
Managing Director
Ph:07952338417
Email:info@brisk-fixwell.com
Web:www.brisk-fixwell.com
So we have our logo, you don’t need to change the logo.
Please see the attachment.
Thanks

Target Market(s)

Home improvement

Industry/Entity Type

Home Improvement

Contact Information for Business Card

Company name: Brisk Fixwell
Name: Faridoullan Mestor
Position: Director
Ph:07952338417
Web: www.brisk-fixwell.com
Add: 42 Corvale Road
Hounslow
TW3 9KD
SECOND PERSON
Nizamuddel mestor
Position: Handyman
Ph: 07812 564037
Email: info@brisk-fixwell.com
Add: 18 Brackwin Lane Road
Hounslow
TW6 2LB

```html
<!DOCTYPE html>
<html lang="en">
<head>
<meta charset="UTF-8">
<title>Brisk Fixwell – Business Card</title>
<link rel="stylesheet" href="https://fonts.googleapis.com/css2?family=Saira+Semi+Condensed:wght@600;700&family=Roboto:wght@400&display=swap">
<style>
  :root {
    --page-bg: #d8d5d1;
    --card-bg: #eef0f3;
    --navy: #24266b;
    --red: #d3292b;
    --ink: #363636;
    --band-text: #e4e5ef;
  }
  html, body {
    margin: 0;
    padding: 0;
    width: 1200px;
    height: 1054px;
    overflow: hidden;
    background: var(--page-bg);
  }
  .card {
    position: absolute;
    left: 100px;
    top: 225px;
    width: 1000px;
    height: 604px;
    background: var(--card-bg);
    border-radius: 18px;
    overflow: hidden;
    box-shadow: 0 6px 24px rgba(0,0,0,0.12);
  }
  .brand {
    position: absolute;
    left: 52px;
    top: 92px;
    display: flex;
    align-items: center;
    gap: 28px;
  }
  .brand-name {
    font-family: "Saira Semi Condensed", sans-serif;
    font-weight: 700;
    font-size: 84px;
    line-height: 1;
    color: var(--navy);
    letter-spacing: -1px;
  }
  .brand-mark {
    width: 92px;
    height: 92px;
    border-radius: 50%;
    background: var(--navy);
  }
  .person {
    position: absolute;
    left: 50px;
    top: 405px;
  }
  .person-name {
    font-family: "Saira Semi Condensed", sans-serif;
    font-weight: 700;
    font-size: 33px;
    line-height: 1.1;
    color: var(--navy);
  }
  .person-role {
    font-family: "Roboto", sans-serif;
    font-size: 24px;
    color: var(--ink);
    margin-top: 6px;
  }
  .contacts {
    position: absolute;
    left: 530px;
    top: 370px;
    list-style: none;
    margin: 0;
    padding: 0;
    font-family: "Roboto", sans-serif;
    font-size: 24px;
    color: var(--ink);
  }
  .contacts li {
    display: flex;
    align-items: center;
    height: 38px;
  }
  .contacts svg {
    width: 22px;
    height: 22px;
    margin-right: 24px;
    fill: var(--red);
  }
  .footer-bands {
    position: absolute;
    left: 0;
    bottom: 0;
    width: 1000px;
    height: 74px;
  }
  .tagline {
    position: absolute;
    left: 453px;
    right: 0;
    bottom: 20px;
    text-align: center;
    font-family: "Roboto", sans-serif;
    font-size: 23px;
    color: var(--band-text);
  }
</style>
</head>
<body>
  <div class="card">
    <div class="brand">
      <span class="brand-name">Brisk Fixwell</span>
      <span class="brand-mark"></span>
    </div>

    <div class="person">
      <div class="person-name">Faridoullan Mestor</div>
      <div class="person-role">Managing Director</div>
    </div>

    <ul class="contacts">
      <li>
        <svg viewBox="0 0 24 24" aria-hidden="true"><path d="M6.6 10.8a15.1 15.1 0 0 0 6.6 6.6l2.2-2.2a1 1 0 0 1 1-.25 11.4 11.4 0 0 0 3.6.57 1 1 0 0 1 1 1V20a1 1 0 0 1-1 1A17 17 0 0 1 3 4a1 1 0 0 1 1-1h3.5a1 1 0 0 1 1 1c0 1.25.2 2.45.57 3.57a1 1 0 0 1-.25 1z"/></svg>
        07952338417
      </li>
      <li>
        <svg viewBox="0 0 24 24" aria-hidden="true"><path d="M2 5h20v14H2z M3.5 6.5 12 12.5l8.5-6z" fill-rule="evenodd"/></svg>
        info@brisk-fixwell.com
      </li>
      <li>
        <svg viewBox="0 0 24 24" aria-hidden="true"><path d="M12 2a10 10 0 1 0 0 20 10 10 0 0 0 0-20zm6.9 9h-3a15 15 0 0 0-1.3-5.6A8 8 0 0 1 18.9 11zM12 4c.9 1.2 1.8 3.6 2 7h-4c.2-3.4 1.1-5.8 2-7zM9.4 5.4A15 15 0 0 0 8.1 11h-3a8 8 0 0 1 4.3-5.6zM5.1 13h3a15 15 0 0 0 1.3 5.6A8 8 0 0 1 5.1 13zM12 20c-.9-1.2-1.8-3.6-2-7h4c-.2 3.4-1.1 5.8-2 7zm2.6-1.4a15 15 0 0 0 1.3-5.6h3a8 8 0 0 1-4.3 5.6z"/></svg>
        www.brisk-fixwell.com
      </li>
    </ul>

    <svg class="footer-bands" viewBox="0 0 1000 74" aria-hidden="true">
      <rect x="0" y="51" width="460" height="23" fill="var(--red)"/>
      <path d="M453 0H1000V74H402Z" fill="var(--navy)"/>
    </svg>
    <div class="tagline">Guarantee Arrival on Time</div>
  </div>
</body>
</html>
```